Copper Lantern

Need a business card for our restaurant. Restaurant and Bar in the mountains of North Idaho. Rustic looking card

rustic design, wood and metal looking, primarily neutral colors

• Name, address, phone number, website, email address

```html
<!DOCTYPE html>
<html lang="en">
<head>
<meta charset="utf-8">
<title>Copper Lantern – Business Card</title>
<link href="https://fonts.googleapis.com/css2?family=Montserrat:wght@400;600;700&display=swap" rel="stylesheet">
<style>
  :root {
    --page-bg: #d9d3c9;
    --card-bg: #ebe6de;
    --card-edge: #f6f3ee;
    --ink: #1b1a18;
    --ink-soft: #2a2825;
  }
  * { box-sizing: border-box; margin: 0; padding: 0; }
  html, body {
    width: 1200px;
    height: 1047px;
    overflow: hidden;
    background: var(--page-bg);
    font-family: "Montserrat", Arial, sans-serif;
    color: var(--ink);
  }
  .business-card {
    position: absolute;
    left: 100px;
    top: 251px;
    width: 1000px;
    height: 545px;
    background: var(--card-bg);
    border: 2px solid var(--card-edge);
    border-radius: 26px;
    box-shadow: 0 10px 30px rgba(60, 50, 40, 0.18);
  }
  .edge-bar {
    position: absolute;
    top: 123px;
    width: 36px;
    height: 298px;
    background: var(--ink);
  }
  .edge-bar--left { left: 0; }
  .edge-bar--right { right: 0; }
  .brand-seal {
    position: absolute;
    left: 141px;
    top: 116px;
    width: 312px;
    height: 312px;
    border: 5px solid var(--ink);
    border-radius: 50%;
    display: flex;
    align-items: center;
    justify-content: center;
    text-align: center;
  }
  .brand-name {
    font-weight: 600;
    font-size: 38px;
    line-height: 1.2;
    letter-spacing: 2px;
    text-transform: uppercase;
    color: var(--ink);
  }
  .divider {
    position: absolute;
    left: 494px;
    top: 125px;
    width: 2px;
    height: 296px;
    background: var(--ink);
  }
  .contact-block {
    position: absolute;
    left: 537px;
    top: 122px;
  }
  .person-name {
    font-weight: 700;
    font-size: 41px;
    line-height: 1;
    letter-spacing: 0.5px;
  }
  .person-role {
    margin-top: 12px;
    font-size: 25px;
    color: var(--ink-soft);
  }
  .address {
    margin-top: 24px;
    font-size: 26px;
    line-height: 38px;
    color: var(--ink-soft);
  }
  .contact-list {
    list-style: none;
    margin-top: 18px;
  }
  .contact-item {
    display: flex;
    align-items: center;
    gap: 12px;
    font-size: 26px;
    line-height: 38px;
    color: var(--ink-soft);
  }
  .contact-icon {
    width: 22px;
    height: 22px;
    fill: var(--ink);
    flex: none;
  }
</style>
</head>
<body>
  <main class="business-card">
    <div class="edge-bar edge-bar--left"></div>
    <div class="edge-bar edge-bar--right"></div>

    <div class="brand-seal">
      <p class="brand-name">Copper<br>Lantern</p>
    </div>

    <div class="divider"></div>

    <section class="contact-block">
      <h1 class="person-name">Owen Hartley</h1>
      <p class="person-role">Managing Director</p>
      <p class="address">Your address, City<br>State, Zip 1234</p>
      <ul class="contact-list">
        <li class="contact-item">
          <svg class="contact-icon" viewBox="0 0 24 24" aria-hidden="true">
            <path d="M3 9c0-3 4-5 9-5s9 2 9 5v2h-5V8.5c-1-.6-2.5-.9-4-.9s-3 .3-4 .9V11H3z"/>
            <path d="M6 12h12l2 8H4z"/>
          </svg>
          <span>123 456 789</span>
        </li>
        <li class="contact-item">
          <svg class="contact-icon" viewBox="0 0 24 24" aria-hidden="true">
            <path d="M2 5h20v2l-10 6L2 7z"/>
            <path d="M2 9l10 6 10-6v10H2z"/>
          </svg>
          <span>info@yourmail.com</span>
        </li>
        <li class="contact-item">
          <svg class="contact-icon" viewBox="0 0 24 24" aria-hidden="true">
            <circle cx="12" cy="12" r="10"/>
            <path d="M7 7c2 0 3 1 3 3s-2 2-2 4 1 3 0 5c-3-1-5-4-5-7 0-2 1-4 4-5zM15 5c2 1 4 3 4 6-1 0-2-1-3 0s0 3-2 4-2-2-2-4 2-3 3-6z" fill="#ebe6de"/>
          </svg>
          <span>www.yourwebsite.com</span>
        </li>
      </ul>
    </section>
  </main>
</body>
</html>
```